Business Cards - Brightpath Horizon

need to design unique business card for my mortgage business. I need to design credit card style business card for my business or any unique idea that you might have

Target Market(s)

Home Loan customers

Industry/Entity Type

Mortgage Brokerage

Contact Information for Business Card

please design credit card style or very unique style business card

Colors

Designer to choose colors to be used in the design.

Requirements
Must have
• Name
• position
• Phone number
• fax number
• email address
• website address
• social media address
• All above fields will be provided once design in finalised

```html
<!DOCTYPE html>
<html lang="en">
<head>
<meta charset="utf-8">
<title>Brightpath Horizon – Business Card</title>
<link rel="stylesheet" href="https://fonts.googleapis.com/css2?family=Roboto:wght@400;500;700&family=Share+Tech+Mono&family=Tinos:wght@700&display=swap">
<style>
  :root {
    --bg: #d9d4cd;
    --card: #f6f6f5;
    --blue: #1b3fbf;
    --orange: #f39a1c;
    --ink: #4a4a4a;
    --digits: #505050;
    --rule: #8c8c8c;
    --dot: #9aa7c9;
  }
  * { margin: 0; padding: 0; box-sizing: border-box; }
  html, body { width: 1200px; height: 969px; overflow: hidden; }
  body {
    background: var(--bg);
    font-family: "Roboto", Arial, sans-serif;
    position: relative;
  }
  .card {
    position: absolute;
    left: 120px; top: 182px;
    width: 960px; height: 605px;
    background: var(--card);
    border-radius: 32px;
    box-shadow: 0 10px 30px rgba(0,0,0,0.15);
  }
  .holder { position: absolute; left: 40px; top: 58px; }
  .holder-name {
    color: var(--blue); font-weight: 700; font-size: 30px; letter-spacing: 0.5px;
    text-transform: uppercase;
  }
  .holder-role {
    color: var(--orange); font-weight: 500; font-size: 22px; margin-top: 4px;
  }
  .brand {
    position: absolute; right: 52px; top: 78px;
    display: flex; align-items: center; gap: 14px;
  }
  .brand-dot { width: 26px; height: 26px; border-radius: 50%; background: var(--orange); }
  .brand-name { color: var(--blue); font-weight: 700; font-size: 34px; }
  .card-number {
    position: absolute; left: 38px; top: 205px;
    font-family: "Share Tech Mono", monospace;
    font-size: 66px; color: var(--digits); letter-spacing: 6px; word-spacing: 34px;
  }
  .contacts {
    position: absolute; left: 40px; top: 380px;
    list-style: none; font-size: 23px; color: var(--ink); line-height: 30px;
  }
  .contacts b {
    font-family: "Tinos", "Times New Roman", serif; color: var(--blue); font-weight: 700;
    margin-right: 6px;
  }
  .address {
    position: absolute; right: 44px; top: 410px;
    text-align: right; font-size: 23px; color: var(--ink); line-height: 30px; font-style: normal;
  }
  .social {
    position: absolute; left: 40px; right: 40px; top: 506px;
    display: flex; align-items: center; gap: 10px;
  }
  .social-rule { flex: 1; height: 1px; background: var(--rule); }
  .social-dot { width: 44px; height: 44px; border-radius: 50%; background: var(--dot); }
</style>
</head>
<body>
  <section class="card">
    <div class="holder">
      <p class="holder-name">Daniel Reyes</p>
      <p class="holder-role">CEO/FOUNDER</p>
    </div>

    <div class="brand">
      <span class="brand-dot"></span>
      <span class="brand-name">Brightpath Horizon</span>
    </div>

    <p class="card-number">531 806 4792</p>

    <ul class="contacts">
      <li><b>P:</b>907 315 6284</li>
      <li><b>E:</b>hello@brightpathhz.com</li>
      <li><b>W:</b>www.brightpathhz.com</li>
    </ul>

    <address class="address">
      2194 Willow Bend Road<br>
      Fairbanks, Alaska 99701
    </address>

    <div class="social" aria-label="Social media links">
      <span class="social-rule"></span>
      <span class="social-dot"></span>
      <span class="social-dot"></span>
      <span class="social-dot"></span>
      <span class="social-dot"></span>
      <span class="social-rule"></span>
    </div>
  </section>
</body>
</html>
```